Velvet Moon Wheel Method Needs a Website

I require a Wordpress website so that I can do simple edits myself. I want it to be a fairly simple design as the videos and the text will speak for themselves.
The concept is simple, we have developed a revolutionary roulette system that proves the game is NOT random. This breakthrough is absolutely massive. We are offering a 12-part training course to take a beginner to a professional at their own pace through watching videos made by our roulette genius.
Roulette and casinos have a glitzy feel about them and this should be reflected in the style of the site. The roulette wheel, table and chips are very evocative and pictures of these would be good.
There is a home page and 5 other pages containing sub-pages. These should be interlinked and it must be easy to get back to the home page from anywhere on the site.
Coinvey links should appear at the bottom of each page.
I really need the site in a hurry as we were let down badly by the last developer we hired who went on holiday and left us in the lurch.

Target Market(s)

Gamblers, betting community, opportunity seekers

Coding

Coded - Design and coding required

Number of Pages Required

1 page

Font styles to use
Sans Serif

Requirements
Must have
• At least two videos on the Home page.
• Coinvey details on every page and tab.
• A box for name and email address for interested parties to leave their details.

```html
<!DOCTYPE html>
<html lang="en">
<head>
<meta charset="utf-8">
<title>Velvet Moon Wheel Method</title>
<link rel="stylesheet" href="https://fonts.googleapis.com/css2?family=Montserrat:wght@300;400;500;600;700&family=Open+Sans:wght@400;600&display=swap">
<style>
:root{
  --pink:#e0245e;
  --pink-dark:#c81d52;
  --navy:#0e1a3d;
  --navy-deep:#0b1535;
  --blue:#3f73e0;
  --ink:#222634;
  --muted:#6b6f7c;
  --grey-bg:#efefef;
  --white:#ffffff;
}
*{box-sizing:border-box;margin:0;padding:0}
html,body{width:1200px;height:3383px;overflow:hidden;background:var(--white)}
body{font-family:"Open Sans",Arial,sans-serif;color:var(--ink);position:relative}
section,header,footer{position:absolute;left:0;width:1200px}

/* header */
.site-header{top:0;height:90px;background:var(--white);z-index:2;overflow:hidden}
.brand{position:absolute;left:81px;top:26px;font-family:"Montserrat",sans-serif;font-weight:700;font-size:30px;color:var(--pink);letter-spacing:1px;white-space:nowrap}
.nav-active{position:absolute;left:431px;top:-86px;width:176px;height:176px;border-radius:50%;background:var(--pink)}
.nav-item{position:absolute;top:36px;font-family:"Montserrat",sans-serif;font-size:14px;font-weight:500;color:var(--ink);text-transform:uppercase;white-space:nowrap}
.nav-item.is-active{color:var(--white);left:431px;width:176px;text-align:center;font-size:13px}

/* hero */
.hero{top:90px;height:544px}
.hero-photo{position:absolute;inset:0;background:radial-gradient(ellipse at 65% 40%,#8a6a3a 0%,#3a3550 30%,#141a35 65%,#0a0f24 100%)}
.hero-title{position:absolute;left:81px;top:196px;font-family:"Montserrat",sans-serif;font-size:44px;font-weight:500;color:var(--white)}
.hero-sub{position:absolute;left:81px;top:250px;font-family:"Montserrat",sans-serif;font-size:27px;font-weight:500;color:var(--pink)}
.hero-dots{position:absolute;left:535px;top:508px;display:flex;gap:12px}
.hero-dots span{width:11px;height:11px;border:2px solid var(--white);border-radius:50%}
.hero-dots span.on{background:var(--white)}

/* welcome */
.welcome{top:634px;height:417px}
.welcome-kicker{position:absolute;left:81px;top:52px;font-family:"Montserrat",sans-serif;font-size:34px;font-weight:300;color:var(--ink)}
.welcome-title{position:absolute;left:81px;top:96px;font-family:"Montserrat",sans-serif;font-size:32px;font-weight:500;color:var(--pink)}
.welcome-text{position:absolute;left:81px;top:150px;width:520px;font-size:13px;line-height:22px;color:var(--muted)}
.video-btn{position:absolute;left:81px;top:284px;width:280px;height:68px;border-radius:16px;background:linear-gradient(90deg,var(--pink-dark),var(--pink));color:var(--white);padding:10px 0 0 40px;font-family:"Montserrat",sans-serif}
.video-btn strong{display:block;font-size:23px;font-weight:500}
.video-btn small{display:block;font-size:12px;margin-top:-2px}
.video-btn svg{position:absolute;right:20px;top:24px}
.welcome-photo{position:absolute;left:638px;top:54px;width:481px;height:307px;background:radial-gradient(circle at 45% 55%,#6a5a7a 0%,#2a3a6a 45%,#12183a 100%)}

/* training */
.training{top:1051px;height:433px;background:linear-gradient(180deg,#17224a,var(--navy-deep))}
.section-title{position:absolute;left:0;width:1200px;text-align:center;font-family:"Montserrat",sans-serif;font-size:30px;font-weight:500;color:var(--pink)}
.feature{position:absolute;top:126px;width:240px;text-align:center}
.feature svg{display:block;margin:0 auto}
.feature-name{margin-top:36px;font-family:"Montserrat",sans-serif;font-size:16px;font-weight:500;color:var(--white);line-height:20px;text-transform:uppercase}
.feature-text{margin-top:10px;font-size:13px;line-height:21px;color:#a9b0c6}

/* casino */
.casino{top:1484px;height:485px}
.casino-tab{position:absolute;left:81px;width:260px;height:54px;border-radius:14px;background:var(--pink);color:var(--white);font-family:"Montserrat",sans-serif;font-size:17px;font-weight:500;padding:15px 0 0 28px}
.casino-tab.is-current{background:var(--blue)}
.casino-panel{position:absolute;left:298px;top:111px;width:821px;height:316px;border-radius:22px;background:var(--blue)}
.casino-photo{position:absolute;left:27px;top:27px;width:282px;height:262px;border-radius:18px;background:linear-gradient(135deg,#2a2f6a,#8a4a6a 55%,#d9a07a)}
.casino-heading{position:absolute;left:327px;top:30px;font-family:"Montserrat",sans-serif;font-size:32px;font-weight:500;color:var(--white)}
.casino-text{position:absolute;left:327px;top:86px;width:464px;font-size:13px;line-height:22px;color:#e6ecfb;text-align:justify}
.small-btn{position:absolute;width:147px;height:41px;border-radius:12px;background:var(--pink);color:var(--white);font-family:"Montserrat",sans-serif;font-size:13px;font-weight:500;text-align:center;line-height:41px}

/* plan */
.plan{top:1969px;height:388px;background:var(--grey-bg)}
.plan-card{position:absolute;top:118px;width:496px;height:214px;border-radius:22px;overflow:hidden}
.plan-card .plan-left{position:absolute;left:0;top:0;width:237px;height:214px;background:linear-gradient(135deg,#2b3350,#141a33);color:var(--white);text-align:center;padding-top:68px;font-family:"Montserrat",sans-serif}
.plan-left strong{display:block;font-size:40px;font-weight:500;line-height:44px}
.plan-left span{display:block;font-size:26px;font-weight:500}
.plan-right{position:absolute;left:237px;top:0;width:259px;height:214px;color:var(--white);text-align:center;padding-top:48px;font-family:"Montserrat",sans-serif}
.plan-right strong{display:block;font-size:62px;font-weight:500;line-height:66px}
.plan-right span{display:block;font-size:26px;line-height:30px}
.plan-right small{display:block;font-size:18px;font-weight:500}

/* vegas */
.vegas{top:2357px;height:508px}
.vegas-photo{position:absolute;inset:0;background:linear-gradient(180deg,#6a88b0 0%,#b8c4cf 40%,#e9c79a 70%,#f2a55a 100%)}
.vegas-sign{position:absolute;left:660px;top:0;width:460px;height:508px;background:radial-gradient(ellipse at 50% 45%,#c23a3a 0%,#8a2a3a 45%,rgba(120,60,60,0) 75%)}
.vegas-title{position:absolute;left:81px;top:198px;font-family:"Montserrat",sans-serif;font-size:38px;font-weight:500;color:var(--navy)}
.vegas-sub{position:absolute;left:81px;top:245px;font-family:"Montserrat",sans-serif;font-size:24px;font-weight:500;color:var(--pink)}
.vegas-text{position:absolute;left:81px;top:286px;width:520px;font-size:15px;line-height:22px;color:#3a3f4d}

/* signup */
.signup{top:2865px;height:244px;background:var(--pink)}
.signup-title{position:absolute;left:0;width:1200px;top:50px;text-align:center;font-family:"Montserrat",sans-serif;font-size:28px;font-weight:400;color:var(--white)}
.signup-title strong{font-weight:600}
.signup-note{position:absolute;left:0;width:1200px;top:92px;text-align:center;font-size:12px;color:#fbe3ea}
.field{position:absolute;top:142px;width:248px;height:46px;border-radius:23px;background:var(--white);color:#9a9a9a;font-size:12px;padding:15px 0 0 20px}
.signup-btn{position:absolute;left:781px;top:142px;width:212px;height:46px;border-radius:23px;background:var(--navy);color:var(--white);font-family:"Montserrat",sans-serif;font-size:15px;font-weight:600;text-align:center;line-height:46px}

/* footer */
.site-footer{top:3109px;height:274px;background:var(--navy)}
.footer-brand{position:absolute;left:150px;top:56px;font-family:"Montserrat",sans-serif;font-size:30px;font-weight:700;color:var(--pink);letter-spacing:1px;white-space:nowrap}
.social{position:absolute;left:124px;top:146px;display:flex;gap:22px}
.social span{width:16px;height:16px;border-radius:50%;background:#7c86a6}
.copyright{position:absolute;left:110px;top:188px;font-size:11px;color:#8c95b2}
.footer-col{position:absolute;top:50px}
.footer-col h4{font-family:"Montserrat",sans-serif;font-size:14px;font-weight:600;color:var(--pink);margin-bottom:14px;text-transform:uppercase}
.footer-col li{list-style:none;font-size:12px;line-height:25px;color:#c5cbe0}
.pay-name{position:absolute;left:909px;top:52px;font-family:"Montserrat",sans-serif;font-size:30px;font-weight:700;color:var(--white)}
.pay-text{position:absolute;left:909px;top:112px;width:200px;font-size:12px;line-height:19px;color:#c5cbe0}
</style>
</head>
<body>

<header class="site-header">
  <div class="brand">VELVET MOON</div>
  <div class="nav-active"></div>
  <span class="nav-item is-active">Wheel Training</span>
  <span class="nav-item" style="left:656px">Casinos</span>
  <span class="nav-item" style="left:778px">Coaching</span>
  <span class="nav-item" style="left:914px">Las Vegas</span>
  <span class="nav-item" style="left:1051px">Contact</span>
</header>

<section class="hero">
  <div class="hero-photo" role="img" aria-label="Close-up photograph of a spinning roulette wheel under casino lights"></div>
  <h1 class="hero-title">When you think of Las Vegas!</h1>
  <p class="hero-sub">you think of Las Vegas casinos.</p>
  <div class="hero-dots"><span class="on"></span><span></span><span></span><span></span><span></span></div>
</section>

<section class="welcome">
  <h2 class="welcome-kicker">Welcome to</h2>
  <p class="welcome-title">Velvet Moon Wheel Method</p>
  <p class="welcome-text">Introducing the incredible Velvet Moon roulette system. Four years in the making by a roulette genius who has observed hundreds of thousands of spins to create a truly groundbreaking system. Every aspect of the game has been broken down, analysed and rebuilt with a solution. This system questions whether the game of roulette is truly random......and the answer is a resounding NO !!</p>
  <div class="video-btn">
    <strong>Watch this video</strong>
    <small>and prepare to be amazed</small>
    <svg width="20" height="20" viewBox="0 0 20 20"><path d="M2 10h14M10 3l7 7-7 7" stroke="#fff" stroke-width="3.5" fill="none"/></svg>
  </div>
  <div class="welcome-photo" role="img" aria-label="Video still of a roulette wheel with a play button"></div>
</section>

<section class="training">
  <h2 class="section-title" style="top:52px">TRAINING</h2>
  <div class="feature" style="left:74px">
    <svg width="110" height="110" viewBox="0 0 110 110"><circle cx="55" cy="55" r="50" fill="none" stroke="#c9cdd8" stroke-width="8" stroke-dasharray="12 9"/><circle cx="55" cy="55" r="38" fill="#e0245e"/><path d="M35 44c8-3 14-2 20 2 6-4 12-5 20-2v24c-8-3-14-2-20 2-6-4-12-5-20-2z" fill="#fff"/><path d="M55 46v24" stroke="#e0245e" stroke-width="2"/></svg>
    <div class="feature-name">Course<br>Description</div>
    <div class="feature-text">The second major breakthrough<br>was the discovery of the families.</div>
  </div>
  <div class="feature" style="left:345px">
    <svg width="110" height="110" viewBox="0 0 110 110"><circle cx="55" cy="55" r="50" fill="none" stroke="#c9cdd8" stroke-width="8" stroke-dasharray="12 9"/><circle cx="55" cy="55" r="38" fill="#e0245e"/><circle cx="55" cy="45" r="10" fill="#fff"/><path d="M37 72c0-11 8-16 18-16s18 5 18 16z" fill="#fff"/></svg>
    <div class="feature-name">Monthly<br>Membership</div>
    <div class="feature-text">The second major breakthrough<br>was the discovery of the families.</div>
  </div>
  <div class="feature" style="left:615px">
    <svg width="110" height="110" viewBox="0 0 110 110"><circle cx="55" cy="55" r="50" fill="none" stroke="#c9cdd8" stroke-width="8" stroke-dasharray="12 9"/><circle cx="55" cy="55" r="38" fill="#e0245e"/><rect x="40" y="36" width="30" height="38" rx="3" fill="#fff"/><rect x="48" y="32" width="14" height="7" rx="2" fill="#fff"/><path d="M46 55l6 6 11-12" stroke="#e0245e" stroke-width="3.5" fill="none"/></svg>
    <div class="feature-name">Complete<br>System</div>
    <div class="feature-text">The second major breakthrough<br>was the discovery of the families.</div>
  </div>
  <div class="feature" style="left:886px">
    <svg width="110" height="110" viewBox="0 0 110 110"><circle cx="55" cy="55" r="50" fill="none" stroke="#c9cdd8" stroke-width="8" stroke-dasharray="12 9"/><circle cx="55" cy="55" r="38" fill="#e0245e"/><circle cx="55" cy="50" r="12" fill="#fff"/><rect x="49" y="60" width="12" height="11" rx="2" fill="#fff"/><path d="M55 30v-4M36 50h-4M78 50h-4M41 36l-3-3M69 36l3-3" stroke="#fff" stroke-width="3"/></svg>
    <div class="feature-name">Intellectual<br>Property Rights</div>
    <div class="feature-text">The second major breakthrough<br>was the discovery of the families.</div>
  </div>
</section>

<section class="casino">
  <h2 class="section-title" style="top:42px">CASINO</h2>
  <div class="casino-tab is-current" style="top:111px">Reputable casino</div>
  <div class="casino-tab" style="top:174px">Casino bonuses</div>
  <div class="casino-tab" style="top:235px">RNG Vs Real wheel</div>
  <div class="casino-panel">
    <div class="casino-photo" role="img" aria-label="Photograph of a player holding a hand of playing cards"></div>
    <h3 class="casino-heading">Velvet Moon at Roulette</h3>
    <p class="casino-text">Introducing the incredible Velvet Moon roulette system. Four years in the making by a roulette genius who has observed hundreds of thousands of spins to create a truly groundbreaking system. Every aspect of the game has been broken down, analysed and rebuilt with a solution. This system questions whether the game of roulette is truly random......and the answer is a resounding NO !!</p>
    <div class="small-btn" style="left:329px;top:248px">More detials</div>
  </div>
</section>

<section class="plan">
  <h2 class="section-title" style="top:40px">OUR PLAN</h2>
  <div class="plan-card" style="left:81px">
    <div class="plan-left" role="img" aria-label="Dark roulette table photograph behind the plan name"><strong>Monthly</strong><span>Subscription</span></div>
    <div class="plan-right" style="background:var(--pink)"><strong>£100</strong><span>GBP</span><small>for each month</small></div>
  </div>
  <div class="plan-card" style="left:623px">
    <div class="plan-left" role="img" aria-label="Dark roulette table photograph behind the plan name"><strong>Single</strong><span>Payment</span></div>
    <div class="plan-right" style="background:var(--blue)"><strong>£1000</strong><span>GBP</span><small>one time payment</small></div>
  </div>
</section>

<section class="vegas">
  <div class="vegas-photo" role="img" aria-label="Las Vegas welcome sign against a sunset sky"></div>
  <div class="vegas-sign"></div>
  <h2 class="vegas-title">When you think of Las Vegas!</h2>
  <p class="vegas-sub">you think of Las Vegas casinos.</p>
  <p class="vegas-text">They've been glorified in films and on the small screen. And for good reason.</p>
</section>

<section class="signup">
  <h2 class="signup-title">Know the latest news by Signup on <strong>Velvet Moon Wheel Method</strong></h2>
  <p class="signup-note">Donec vulputate, urna ut volutpat pretium, quam diam varius nunc, sed fermentum tortor urna sed nulla nulla vel magna viverra</p>
  <div class="field" style="left:266px">Enter Your Email Address</div>
  <div class="field" style="left:526px">Password</div>
  <div class="signup-btn">Signup</div>
</section>

<footer class="site-footer">
  <div class="footer-brand">VELVET MOON</div>
  <div class="social"><span></span><span></span><span></span><span></span><span></span></div>
  <p class="copyright">© 2016 Copyrights. All Rights Reserved</p>
  <div class="footer-col" style="left:435px">
    <h4>Main Menu</h4>
    <ul><li>Home</li><li>Wheel Training</li><li>Casinos</li><li>Coaching</li><li>Las Vegas</li></ul>
  </div>
  <div class="footer-col" style="left:681px">
    <h4>Quick Links</h4>
    <ul><li>Services</li><li>Contact us</li><li>Free Consultation</li><li>Specials</li><li>Special Offers</li></ul>
  </div>
  <div class="pay-name">Coinvey</div>
  <p class="pay-text">Lorem ipsum dolor sit amet, consectetur adipiscing elit.</p>
  <div class="small-btn" style="left:909px;top:172px;width:106px;height:30px;line-height:30px;font-size:11px">More detials</div>
</footer>

</body>
</html>
```